Business card design for Virtual Assistance company

I need a business card designed for my virtual assistance company. We are a small company who services primarily C-level executive clients. The card needs to be double sided with the following contact information on the back:
Melissa Thornbury
Owner/CEO
info@rkpadvisory.net
www.rkpadvisory.net
555.302.9817

The front side should just have the company name incorporated: "RKP Advisory" and "virtual assistance"

The card should be simplistic, but eye catching and should speak to high level executives. Our primary focus areas consist of executive assistance and government contracting.

Target Market(s)

CEOs and executives

Contact Information for Business Card

see project description. phone, email, website.

Colors

Designer to choose only greyscale colors for use in the design.

```html
<!DOCTYPE html>
<html lang="en">
<head>
<meta charset="utf-8">
<title>RKP Advisory business card</title>
<link rel="stylesheet" href="https://fonts.googleapis.com/css2?family=Poppins:wght@400;600&display=swap">
<style>
  :root {
    --backdrop: #424242;
    --card: #ffffff;
    --ink: #3a3a3a;
    --accent: #b4b4b4;
    --rule: #d4d4d4;
  }
  * { box-sizing: border-box; margin: 0; padding: 0; }
  html, body { width: 960px; height: 1200px; overflow: hidden; }
  body {
    background: var(--backdrop);
    font-family: "Poppins", sans-serif;
    color: var(--ink);
    display: flex;
    flex-direction: column;
    align-items: center;
    justify-content: center;
    gap: 80px;
  }
  .card {
    position: relative;
    width: 760px;
    height: 434px;
    background: var(--card);
  }
  .card-front {
    display: flex;
    align-items: center;
    justify-content: center;
  }
  .brand-block {
    display: flex;
    flex-direction: column;
    align-items: center;
  }
  .brand {
    display: flex;
    align-items: center;
    gap: 18px;
    font-weight: 600;
    color: var(--ink);
    white-space: nowrap;
  }
  .brand-square {
    display: block;
    background: var(--accent);
  }
  .tagline {
    font-weight: 600;
    color: var(--accent);
    text-transform: uppercase;
    white-space: nowrap;
  }
  .brand-front { font-size: 50px; letter-spacing: 1px; line-height: 1.2; }
  .brand-front .brand-square { width: 26px; height: 26px; }
  .tagline-front { font-size: 14px; letter-spacing: 8px; margin-top: 10px; padding-left: 8px; }
  .brand-block-back {
    position: absolute;
    left: 170px;
    top: 217px;
    transform: translate(-50%, -50%);
  }
  .brand-back { font-size: 28px; gap: 12px; line-height: 1.2; }
  .brand-back .brand-square { width: 15px; height: 15px; }
  .tagline-back { font-size: 9px; letter-spacing: 4px; margin-top: 6px; padding-left: 4px; }
  .divider {
    position: absolute;
    left: 333px;
    top: 94px;
    width: 1.5px;
    height: 244px;
    background: var(--rule);
  }
  .details {
    position: absolute;
    left: 390px;
    top: 108px;
  }
  .holder-name {
    font-size: 24px;
    font-weight: 600;
    letter-spacing: 0.8px;
    line-height: 1.2;
    text-transform: uppercase;
  }
  .holder-title {
    font-size: 15px;
    font-weight: 400;
    letter-spacing: 1px;
    color: var(--accent);
    text-transform: uppercase;
    margin-top: 2px;
  }
  .contacts {
    list-style: none;
    margin-top: 62px;
  }
  .contacts li {
    display: flex;
    align-items: center;
    gap: 14px;
    font-size: 16px;
    letter-spacing: 1.2px;
    height: 33px;
  }
  .contacts svg { width: 14px; height: 14px; flex: none; fill: var(--accent); }
</style>
</head>
<body>
  <section class="card card-front" aria-label="Card front">
    <div class="brand-block">
      <div class="brand brand-front"><span class="brand-square"></span>RKP Advisory</div>
      <p class="tagline tagline-front">Virtual Assistance</p>
    </div>
  </section>

  <section class="card card-back" aria-label="Card back">
    <div class="brand-block brand-block-back">
      <div class="brand brand-back"><span class="brand-square"></span>RKP Advisory</div>
      <p class="tagline tagline-back">Virtual Assistance</p>
    </div>
    <div class="divider"></div>
    <div class="details">
      <h1 class="holder-name">Melissa Thornbury</h1>
      <p class="holder-title">Owner/CEO</p>
      <ul class="contacts">
        <li>
          <svg viewBox="0 0 24 24" aria-hidden="true"><path d="M6.6 10.8a15.1 15.1 0 0 0 6.6 6.6l2.2-2.2a1 1 0 0 1 1-.25 11.4 11.4 0 0 0 3.6.57 1 1 0 0 1 1 1V20a1 1 0 0 1-1 1A17 17 0 0 1 3 4a1 1 0 0 1 1-1h3.5a1 1 0 0 1 1 1c0 1.25.2 2.45.57 3.57a1 1 0 0 1-.25 1z"/></svg>
          555.302.9817
        </li>
        <li>
          <svg viewBox="0 0 24 24" aria-hidden="true"><path d="M2 5h20v14H2z" opacity=".6"/><path d="M2 5l10 8 10-8v2l-10 8L2 7z"/></svg>
          info@rkpadvisory.net
        </li>
        <li>
          <svg viewBox="0 0 24 24" aria-hidden="true"><circle cx="12" cy="12" r="10"/><path d="M7 7c2 1 3 3 2 5s1 3 3 3v4c-3-1-6-4-6-8 0-2 0-3 1-4zM14 5c2 0 4 2 4 4-2 0-3 1-4 0s-1-2 0-4z" fill="#fff"/></svg>
          www.rkpadvisory.net
        </li>
      </ul>
    </div>
  </section>
</body>
</html>
```